Coastline Premier Retreats Business Card Design

Design a business card for Coastline Premier Retreats. Look at the website for colors and reference. Card should have logo, name, title, office number, mobile number, email, URL and a tagline like, "Luxury Hotel & Resort Email Marketing" (This might change).

https://www.coastlinepremierretreats.example

The rest I will leave up to your imagination.

Contact Information for Business Card

Logo, name, title, office number, mobile number, email, URL and a tagline like, "Luxury Hotel & Resort Email Marketing" (This might change).

```html
<!DOCTYPE html>
<html lang="en">
<head>
<meta charset="UTF-8">
<title>Coastline Premier Retreats – Business Card</title>
<link href="https://fonts.googleapis.com/css2?family=Josefin+Sans:wght@400;600;700&display=swap" rel="stylesheet">
<style>
  :root {
    --backdrop: #2b2b2c;
    --card: #ffffff;
    --card-shade: #ececec;
    --ink: #141414;
    --muted: #3a3a3a;
    --accent: #e8711f;
    --band: #0b0b0b;
  }
  * { box-sizing: border-box; margin: 0; padding: 0; }
  html, body { width: 1200px; height: 900px; overflow: hidden; }
  body {
    background: var(--backdrop);
    font-family: "Josefin Sans", sans-serif;
    position: relative;
  }
  .card {
    position: absolute;
    width: 600px;
    height: 343px;
    background: linear-gradient(120deg, var(--card-shade) 0%, var(--card) 55%, var(--card) 100%);
    box-shadow: 0 12px 30px rgba(0,0,0,.45);
  }
  .card--front { left: 90px; top: 70px; }
  .card--back { left: 510px; top: 480px; }

  .wordmark {
    display: flex;
    align-items: center;
    gap: 10px;
    color: var(--ink);
    font-weight: 700;
    text-transform: uppercase;
    letter-spacing: 1px;
    white-space: nowrap;
  }
  .wordmark__square {
    width: 14px; height: 14px;
    background: var(--accent);
    flex: none;
  }
  .card--front .wordmark {
    position: absolute;
    left: 0; right: 0; top: 155px;
    justify-content: center;
    font-size: 27px;
  }
  .card--back .wordmark {
    position: absolute;
    right: 40px; top: 42px;
    font-size: 19px;
  }

  .person {
    position: absolute;
    left: 40px; top: 150px;
  }
  .person__name {
    color: var(--accent);
    font-weight: 700;
    font-size: 21px;
    letter-spacing: .5px;
    text-transform: uppercase;
  }
  .person__title {
    color: var(--muted);
    font-size: 15px;
    margin-top: 4px;
  }
  .contact-row {
    display: flex;
    align-items: center;
    gap: 8px;
    color: var(--muted);
    font-size: 14px;
    line-height: 1;
  }
  .person .contact-row { margin-top: 8px; margin-left: 16px; }
  .contact-row svg { width: 14px; height: 14px; flex: none; }

  .contact-list {
    position: absolute;
    left: 56px; bottom: 26px;
    display: flex;
    flex-direction: column;
    gap: 9px;
  }

  .tagline-band {
    position: absolute;
    right: 0; top: 212px;
    width: 322px; height: 38px;
    background: var(--band);
    color: var(--accent);
    font-size: 14px;
    display: flex;
    align-items: center;
    padding-left: 18px;
    padding-top: 3px;
  }
</style>
</head>
<body>

  <section class="card card--front">
    <div class="wordmark"><span class="wordmark__square"></span>Coastline Premier Retreats</div>
  </section>

  <section class="card card--back">
    <div class="wordmark"><span class="wordmark__square"></span>Coastline Premier Retreats</div>

    <div class="person">
      <p class="person__name">Daniel Reeve</p>
      <p class="person__title">Director</p>
      <p class="contact-row">
        <svg viewBox="0 0 14 14" aria-hidden="true"><rect x="3.5" y="1" width="7" height="12" rx="1.2" fill="none" stroke="var(--accent)" stroke-width="1.4"/><circle cx="7" cy="11" r=".8" fill="var(--accent)"/></svg>
        300.000.0000
      </p>
    </div>

    <div class="contact-list">
      <p class="contact-row">
        <svg viewBox="0 0 14 14" aria-hidden="true"><path d="M3 1.5l2 2.4-1.2 1.5c.8 1.8 2 3 3.8 3.8L9 8l2.5 2-1 2.3C6 12 2 8 1.7 3.5z" fill="var(--accent)"/></svg>
        555.210.4800
      </p>
      <p class="contact-row">
        <svg viewBox="0 0 14 14" aria-hidden="true"><path d="M7 13s-4.5-5-4.5-8A4.5 4.5 0 0 1 11.5 5c0 3-4.5 8-4.5 8z" fill="var(--accent)"/><circle cx="7" cy="5" r="1.6" fill="#fff"/></svg>
        North America
      </p>
      <p class="contact-row">
        <svg viewBox="0 0 14 14" aria-hidden="true"><rect x="1" y="3" width="12" height="8.5" fill="var(--accent)"/><path d="M1 3l6 5 6-5" fill="none" stroke="#fff" stroke-width="1.1"/></svg>
        info@coastlinepremierretreats.example
      </p>
      <p class="contact-row">
        <svg viewBox="0 0 14 14" aria-hidden="true"><g fill="none" stroke="var(--accent)" stroke-width="1"><circle cx="7" cy="7" r="5.8"/><ellipse cx="7" cy="7" rx="2.6" ry="5.8"/><path d="M1.2 7h11.6M2 4h10M2 10h10"/></g></svg>
        www.coastlinepremierretreats.example
      </p>
    </div>

    <div class="tagline-band">Luxury Hotel &amp; Resort Email Marketing</div>
  </section>

</body>
</html>
```